Modern Business Card for Larkwell 2018

Our company assumes the best about people. We are creating an online community of entrepreneurs and business leaders who struggle with marketing their business online.

This business card should POP! We recently got a new logo and are launching a new website next month, so our business cards should make a statement that feels:
-Fresh
-Smart
-Trustworthy
-Fun

Target Market(s)

small business owners, entrepreneurs

Industry/Entity Type

Digital Marketing

Contact Information for Business Card

Dimensions: 3.5" x 2"

Font styles to use
Sans Serif

Colors
f37122
ffffff

Requirements
Must have
• We need a business card with a modern, bold design. We will use one side of the card as a lead-generation offer, so text on one side will need to fit up to 140 characters. The business card should stick to our core colors (orange, black, and white).
Nice to have
• We think a vertical "portrait" design could be interesting.
Should not have
• Should not look like a traditional business card. The round icon should stand out from a distance.

```html
<!DOCTYPE html>
<html lang="en">
<head>
<meta charset="utf-8">
<title>Larkwell Business Card</title>
<link rel="stylesheet" href="https://fonts.googleapis.com/css2?family=Roboto:wght@400;500;700;900&family=Allura&display=swap">
<style>
  :root {
    --brand-orange: #f26a27;
    --brand-orange-soft: #f8b48f;
    --paper: #f4f4f4;
    --ink: #1e1e1e;
    --white: #ffffff;
    --backdrop: #e2e2e2;
  }
  * { margin: 0; padding: 0; box-sizing: border-box; }
  html, body { width: 1200px; height: 960px; overflow: hidden; }
  body {
    position: relative;
    background: var(--backdrop);
    font-family: "Roboto", Arial, sans-serif;
  }
  .card {
    position: absolute;
    width: 600px;
    height: 343px;
    background: var(--paper);
    overflow: hidden;
    box-shadow: 0 4px 14px rgba(0,0,0,0.18);
  }
  .card--front { left: 302px; top: 118px; }
  .card--back { left: 299px; top: 499px; }

  /* Front */
  .front__decoration {
    position: absolute;
    left: 320px; top: 28px;
    width: 258px; height: 315px;
    background: linear-gradient(160deg, var(--brand-orange) 0%, var(--brand-orange-soft) 100%);
    border-radius: 130px 130px 0 0;
  }
  .identity {
    position: absolute;
    left: 42px; top: 196px;
    width: 254px;
    text-align: center;
  }
  .identity__name {
    font-family: "Allura", cursive;
    font-size: 48px;
    line-height: 1;
    color: var(--brand-orange);
    white-space: nowrap;
    text-align: left;
  }
  .identity__title {
    margin-top: 14px;
    font-size: 16px;
    font-weight: 500;
    color: var(--ink);
    letter-spacing: 0.2px;
  }
  .identity__email {
    margin-top: 3px;
    font-size: 14px;
    color: var(--ink);
  }

  /* Back */
  .offer-band {
    position: absolute;
    left: 0; top: 0;
    width: 600px; height: 219px;
    background: var(--brand-orange);
    color: var(--white);
  }
  .brand {
    position: absolute;
    left: 46px; top: 58px;
    width: 228px;
    text-align: center;
  }
  .brand__dot {
    display: block;
    width: 38px; height: 38px;
    margin: 0 auto 10px;
    border-radius: 50%;
    background: var(--white);
  }
  .brand__name {
    font-size: 37px;
    font-weight: 900;
    letter-spacing: 1px;
    line-height: 1;
  }
  .brand__tagline {
    margin-top: 6px;
    font-size: 10.5px;
    font-weight: 700;
    letter-spacing: 1px;
    text-transform: uppercase;
  }
  .offer-band__divider {
    position: absolute;
    left: 297px; top: 28px;
    width: 1px; height: 165px;
    background: rgba(255,255,255,0.7);
  }
  .offer {
    position: absolute;
    left: 322px; top: 30px;
    width: 260px;
  }
  .offer__headline {
    font-size: 19px;
    font-weight: 700;
    line-height: 21px;
    text-transform: uppercase;
  }
  .offer__body {
    margin-top: 6px;
    font-size: 15.5px;
    line-height: 19.5px;
  }
  .offer__url {
    margin-top: 9px;
    font-size: 19px;
    font-weight: 700;
  }
  .notes { position: absolute; left: 36px; top: 260px; width: 520px; }
  .notes__line { height: 1px; background: var(--ink); margin-bottom: 39px; }
</style>
</head>
<body>
  <section class="card card--front" aria-label="Card front">
    <div class="front__decoration" role="img" aria-label="Large brand symbol decoration in orange"></div>
    <div class="identity">
      <p class="identity__name">Dana Whitfield</p>
      <p class="identity__title">STORY MARKETING COACH</p>
      <p class="identity__email">dana@larkwellhq.com</p>
    </div>
  </section>

  <section class="card card--back" aria-label="Card back">
    <div class="offer-band">
      <div class="brand">
        <span class="brand__dot"></span>
        <p class="brand__name">LARKWELL</p>
        <p class="brand__tagline">Tell stories that inspire action</p>
      </div>
      <div class="offer-band__divider"></div>
      <div class="offer">
        <p class="offer__headline">Reach more people.<br>Make more money.<br>Create more impact.</p>
        <p class="offer__body">Get your free Larkwell<br>Starter Package and our<br>marketing guide today at</p>
        <p class="offer__url">Larkwellhq.com/start</p>
      </div>
    </div>
    <div class="notes">
      <div class="notes__line"></div>
      <div class="notes__line"></div>
    </div>
  </section>
</body>
</html>
```